Business card design for holistic health care clinic

We need a double-sided business card design for our holistic health care clinic that integrates our logo design and also its color scheme. My business is called Valmira. It is an integrative medicine clinic. You have already done the logo for me. Please ensure an elegant and upscale design that is not cluttered, but still has all the necessary information (please see below for details).

Target Market(s)

Wellness, fitness, rehabilitation for educated, well-traveled open-minded clients who are focused on natural, organic, balanced and preventive healthcare and lifestyle.

Industry/Entity Type

Medical

Contact Information for Business Card

Modern, clean.

Number of Pages Required

1 page

Font styles to use
Serif
Sans Serif

Colors

Designer to choose colors to be used in the design.

Requirements
Must have
• Logo on one side, all other information on the other side.
• Other information should include:
• Tobias Wrenfeld - DOE, CPT, LMT
• 4100 East Marrow Drive
• Austin, TX 78119
• 512 555 0148
• 818 555 0192
• info@ValmiraHealth.example
• t.wrenfeld@ValmiraHealth.example
Nice to have
• Darker background on front - but not totally black - shaded/dark gray.

```html
<!DOCTYPE html>
<html lang="en">
<head>
<meta charset="utf-8">
<title>Valmira – Business Card</title>
<link rel="stylesheet" href="https://fonts.googleapis.com/css2?family=Roboto:wght@400;700&family=Roboto+Condensed:wght@700&display=swap">
<style>
  :root {
    --backdrop: #5b4a3b;
    --card-top: #2e2e2e;
    --card-bottom: #232323;
    --brand-blue: #0a8fc7;
    --text-light: #e6e6e6;
    --band-text: #f2f7fa;
  }
  * { margin: 0; padding: 0; box-sizing: border-box; }
  html, body { width: 1200px; height: 960px; overflow: hidden; }
  body {
    background: var(--backdrop);
    font-family: "Roboto", Arial, sans-serif;
    position: relative;
  }
  .card {
    position: absolute;
    width: 600px;
    height: 344px;
    border-radius: 22px;
    background: linear-gradient(180deg, var(--card-top), var(--card-bottom));
    box-shadow: 0 3px 6px rgba(0,0,0,.45);
    overflow: hidden;
  }
  .card-front { left: 315px; top: 113px; }
  .card-back  { left: 311px; top: 472px; }

  .brand-name {
    position: absolute;
    right: 42px;
    top: 70px;
    font-weight: 700;
    font-size: 52px;
    letter-spacing: 1px;
    color: var(--brand-blue);
    line-height: 1;
  }

  .person-name {
    position: absolute;
    left: 34px;
    top: 197px;
    font-family: "Roboto Condensed", "Arial Narrow", sans-serif;
    font-weight: 700;
    font-size: 21px;
    color: var(--brand-blue);
    text-transform: uppercase;
    white-space: nowrap;
  }
  .person-name .credentials { font-size: 12px; margin-left: 2px; }

  .contact-list {
    position: absolute;
    left: 34px;
    top: 237px;
    list-style: none;
    font-size: 15px;
    color: var(--text-light);
  }
  .contact-list li {
    display: flex;
    align-items: center;
    height: 19px;
    white-space: nowrap;
  }
  .contact-list svg {
    width: 14px; height: 14px;
    margin-right: 9px;
    fill: var(--brand-blue);
    flex: none;
  }
  .divider {
    position: absolute;
    left: 312px;
    top: 278px;
    width: 1px;
    height: 31px;
    background: var(--text-light);
  }
  .address {
    position: absolute;
    left: 330px;
    top: 275px;
    font-size: 15px;
    line-height: 19px;
    color: var(--text-light);
    font-style: normal;
    white-space: nowrap;
  }

  .back-brand {
    position: absolute;
    left: 0; right: 0;
    top: 126px;
    text-align: center;
    font-weight: 700;
    font-size: 78px;
    letter-spacing: 3px;
    color: var(--brand-blue);
    line-height: 1;
  }
  .tagline-band {
    position: absolute;
    left: 0; right: 0;
    top: 278px;
    height: 29px;
    background: var(--brand-blue);
    color: var(--band-text);
    font-size: 15px;
    line-height: 29px;
    text-align: center;
  }
</style>
</head>
<body>

<section class="card card-front" aria-label="Card front">
  <div class="brand-name">VALMIRA</div>

  <h1 class="person-name">Tobias Wrenfeld <span class="credentials">- DOE, CPT, LMT</span></h1>

  <ul class="contact-list">
    <li>
      <svg viewBox="0 0 24 24" aria-hidden="true"><path d="M6.6 10.8a15.1 15.1 0 0 0 6.6 6.6l2.2-2.2c.3-.3.7-.4 1-.2 1.1.4 2.3.6 3.6.6.6 0 1 .4 1 1V20c0 .6-.4 1-1 1A17 17 0 0 1 3 4c0-.6.4-1 1-1h3.5c.6 0 1 .4 1 1 0 1.3.2 2.5.6 3.6.1.3 0 .7-.2 1z"/></svg>
      512 555 0148
    </li>
    <li>
      <svg viewBox="0 0 24 24" aria-hidden="true"><path d="M7 1h10a2 2 0 0 1 2 2v18a2 2 0 0 1-2 2H7a2 2 0 0 1-2-2V3a2 2 0 0 1 2-2zm0 3v14h10V4zm5 15.5a1.2 1.2 0 1 0 0 2.4 1.2 1.2 0 0 0 0-2.4z"/></svg>
      818 555 0192
    </li>
    <li>
      <svg viewBox="0 0 24 24" aria-hidden="true"><path d="M2 5h20v14H2zm2 2v.5l8 5 8-5V7zm0 2.8V17h16V9.8l-8 5z"/></svg>
      t.wrenfeld@ValmiraHealth.example
    </li>
    <li>
      <svg viewBox="0 0 24 24" aria-hidden="true"><path d="M12 2a10 10 0 1 0 0 20 10 10 0 0 0 0-20zm-1 17.9A8 8 0 0 1 4.2 10.2L9 15v1c0 1.1.9 2 2 2zm6.9-2.5A2 2 0 0 0 16 16h-1v-3c0-.6-.4-1-1-1H8v-2h2c.6 0 1-.4 1-1V7h2a2 2 0 0 0 2-2v-.4a8 8 0 0 1 2.9 12.8z"/></svg>
      www.ValmiraHealth.example
    </li>
  </ul>

  <span class="divider" aria-hidden="true"></span>
  <address class="address">4100 East Marrow Drive<br>Austin, TX 78119</address>
</section>

<section class="card card-back" aria-label="Card back">
  <div class="back-brand">VALMIRA</div>
  <p class="tagline-band">it’s all about you — your health, your objectives</p>
</section>

</body>
</html>
```